Stylish Business Cards Wanted

- DOUBLE SIDED Design Required -

High end, edgy cards for a corporate and personal stylist. Must include logo,
Name: Belinda Harwick
Title: Director and Stylist
telephone : +61 8 7142 5809
email: belinda@theloombriefing.example
website: theloombriefing.example
Tag: Corporate Workwear & Uniform Specialist | Personal Stylist
Would like nice icons for telephone, email, website

Target Market(s)

Businesses wanting stylish uniforms, people wanting stylish wardrobes

Industry/Entity Type

Corporate Workwear Stylist

Contact Information for Business Card

I would like black, white and gold foiling incorporated in the design - possibly a touch of the other colours on my branding guide attached Name: Belinda Harwick Title: Director and Stylist telephone : +61 8 7142 5809 email: belinda@theloombriefing.example website: theloombriefing.example Tag: Corporate Workwear & Uniform Specialist | Personal Stylist Would like nice icons for telephone, email, website

Font styles to use
Other font styles liked:
• Raleway

Colors

Designer to choose colors to be used in the design.

Requirements
Must have
• Gold foil accents

```html
<!DOCTYPE html>
<html lang="en">
<head>
<meta charset="utf-8">
<title>The Loom Briefing — Business Cards</title>
<link rel="stylesheet" href="https://fonts.googleapis.com/css2?family=Montserrat:wght@400;500&display=swap">
<style>
  :root {
    --backdrop: #d9d9da;
    --card-white: #f6f6f4;
    --card-black: #1f1e1e;
    --ink: #1c1b1b;
    --gold: #d7ac4a;
    --muted: #6b6b6b;
    --rule: #b4b4b4;
    --silver: #e4e4e4;
    --text-font: "Montserrat", sans-serif;
  }
  * { box-sizing: border-box; margin: 0; padding: 0; }
  html, body { width: 1200px; height: 800px; overflow: hidden; }
  body {
    background: var(--backdrop);
    font-family: var(--text-font);
    display: flex;
    align-items: center;
    justify-content: center;
    gap: 48px;
  }
  .card {
    position: relative;
    width: 532px;
    height: 304px;
    border: 2px solid var(--gold);
    box-shadow: 0 14px 30px rgba(0,0,0,0.18);
  }
  /* Front: contact side */
  .card--front { background: var(--card-white); color: var(--ink); }
  .front__brand {
    position: absolute;
    top: 40px;
    right: 40px;
    display: flex;
    align-items: center;
    gap: 10px;
    font-size: 22px;
    font-weight: 500;
    color: var(--ink);
    letter-spacing: 0.02em;
  }
  .brand-dot {
    width: 10px;
    height: 10px;
    background: var(--gold);
  }
  .front__top-rule {
    position: absolute;
    top: 98px;
    left: 40px;
    right: 40px;
    height: 1px;
    background: var(--rule);
  }
  .front__details {
    position: absolute;
    left: 40px;
    bottom: 34px;
    width: 300px;
  }
  .person__name {
    font-size: 17px;
    font-weight: 500;
    text-transform: uppercase;
    letter-spacing: 0.04em;
  }
  .person__title {
    font-size: 12px;
    color: var(--gold);
    margin-top: 3px;
  }
  .details__rule {
    height: 1px;
    background: var(--rule);
    margin: 12px 0 10px;
  }
  .contact-list { list-style: none; }
  .contact-list li {
    display: flex;
    align-items: center;
    gap: 9px;
    font-size: 11px;
    color: var(--muted);
    line-height: 19px;
  }
  .contact-icon { width: 11px; height: 11px; flex: none; }

  /* Back: brand side */
  .card--back { background: var(--card-black); }
  .back__brand {
    position: absolute;
    top: 112px;
    left: 0;
    right: 0;
    text-align: center;
    font-size: 38px;
    font-weight: 500;
    color: var(--silver);
    letter-spacing: 0.02em;
  }
  .back__tagline {
    position: absolute;
    left: 0;
    right: 0;
    bottom: 30px;
    text-align: center;
    font-size: 11px;
    color: #cfcfcf;
    text-transform: uppercase;
    letter-spacing: 0.09em;
  }
  .tagline__divider { color: var(--gold); margin: 0 4px; }
</style>
</head>
<body>

  <section class="card card--front" aria-label="Business card front">
    <div class="front__brand"><span class="brand-dot"></span>The Loom Briefing</div>
    <div class="front__top-rule"></div>

    <div class="front__details">
      <p class="person__name">Belinda Harwick</p>
      <p class="person__title">Director &amp; Stylist</p>
      <div class="details__rule"></div>
      <ul class="contact-list">
        <li>
          <svg class="contact-icon" viewBox="0 0 12 12" aria-hidden="true">
            <path d="M2.4 0.8 L4.2 2.9 L3.3 4.2 C4 5.6 5.3 7 7.8 8.7 L9.1 7.8 L11.2 9.6 L9.8 11.2 C5.5 10.6 1.4 6.5 0.8 2.2 Z" fill="var(--gold)"/>
          </svg>
          +61 8 7142 5809
        </li>
        <li>
          <svg class="contact-icon" viewBox="0 0 12 12" aria-hidden="true">
            <rect x="0.5" y="2" width="11" height="8" fill="var(--gold)"/>
            <path d="M0.8 2.4 L6 6.6 L11.2 2.4" stroke="var(--card-white)" stroke-width="1" fill="none"/>
          </svg>
          belinda@theloombriefing.example
        </li>
        <li>
          <svg class="contact-icon" viewBox="0 0 12 12" aria-hidden="true">
            <circle cx="6" cy="6" r="5.4" fill="var(--gold)"/>
            <ellipse cx="6" cy="6" rx="2.2" ry="5.2" stroke="var(--card-white)" stroke-width="0.8" fill="none"/>
            <line x1="0.8" y1="6" x2="11.2" y2="6" stroke="var(--card-white)" stroke-width="0.8"/>
          </svg>
          theloombriefing.example
        </li>
      </ul>
    </div>
  </section>

  <section class="card card--back" aria-label="Business card back">
    <div class="back__brand">The Loom Briefing</div>
    <p class="back__tagline">
      Corporate Workwear<span class="tagline__divider">|</span>Uniform Specialist<span class="tagline__divider">|</span>Personal Stylist
    </p>
  </section>

</body>
</html>
```